Letterhead Design Project

Based on the attached logo we would like have a designed of stationary.
As we are a management consulting company focused on business development dealing with C-level and one level below we new business cards.
We have decided to use KMR (Kestrel Meridian Rowe) as the business name. The legal name will be Kestrel Meridian Rowe ApS but we will brand us under KMR. The tack line is “Shaping Lasting Gains” if we need one.
For legal reasons we need to have the legal name on the letters together with the company no. (cvr. nr. 58117904)
We want to signal the following:
- Serious
- Professional
- Creating Result
- Capable of thinking out of the box and creative
- Fast reactions we will be there when needed
What we do not want to be view as is:
- To smart
- We know better
- We can fix it yesterday
Our Value Proposition is two sited:
- Increasing revenue
- Reduced sales cost or increased efficiency
Therefore, companies can call us when they want to grow or they need to be more efficient.
Our business cards should have a two sided print with the logo incl. the tack line on one side and the detailed information on the other site.
We need to have the following information on the letter head:
- Legal company name
- Cvr nr.
- Address incl. country name (Denmark)
- Main number
- Wed address
Symbols are welcome to be used to guide for the above information.
The following information are expected to be in the personal signature of the letter.
- Name
- Title
- Mobile number
- E-mail address
Updates
Some of you has requested our specific details so here they come:
- Address incl. country name (Denmark): Lyngvænget 42, 3460 Birkerød, Denmark
- Main number: +45 7081 5532
- Wed address: www.kmrhalo.com
Mobile no. are +45 xxxx xxxx or +45 2287 3104
Our e-mail looks like this: firstname.seconname@KMRHALO.COM or for me: jonas.vallgren@kmrhalo.com
We need the design (file) as finish as posible so we just need to add personal details before printing.
Please be aware that we will prefer designs where we can print the full letter incl. design. As we are communicating on e-mails with pdf versions of the letter we also need to have a design which will print on the clients printers.
Target Market(s)
C level and one level below.
Major local and international Companies.
Industry/Entity Type
Management Consulting
Font styles to use
Colors
Designer to choose colors to be used in the design.
Requirements
Must have
- Use of our logo without tack line

```html
<!DOCTYPE html>
<html lang="en">
<head>
<meta charset="utf-8">
<title>Kestrel Meridian Rowe ApS — Letterhead</title>
<link href="https://fonts.googleapis.com/css2?family=Open+Sans:ital,wght@0,400;0,600;0,700;1,400&family=Kaushan+Script&display=swap" rel="stylesheet">
<style>
  :root {
    --bg: #eeeeee;
    --paper: #ffffff;
    --brand: #0d5aa7;
    --brand-dark: #0a4790;
    --brand-light: #6db3e6;
    --ink: #4a4a4a;
    --ink-soft: #6a6a6a;
    --ghost: #f2f4f7;
  }
  * { box-sizing: border-box; margin: 0; padding: 0; }
  html, body {
    width: 1200px; height: 1076px; overflow: hidden;
    background: var(--bg);
    font-family: "Open Sans", Arial, sans-serif;
  }
  .letterhead {
    position: absolute; left: 246px; top: 38px;
    width: 707px; height: 1000px;
    background: var(--paper);
    box-shadow: 0 4px 18px rgba(0,0,0,0.12);
    overflow: hidden;
  }
  .band { position: absolute; left: 0; width: 707px; height: 14px; display: block; }
  .band--top { top: 0; }
  .band--bottom { bottom: 0; }

  .brand { position: absolute; left: 70px; top: 50px; text-align: center; }
  .brand__name {
    font-size: 46px; font-weight: 700; color: var(--brand);
    letter-spacing: 1px; line-height: 1;
  }
  .brand__cvr {
    margin-top: 8px; font-size: 10px; font-weight: 700;
    color: var(--brand-dark); letter-spacing: 0.3px;
  }
  .divider {
    position: absolute; left: 212px; top: 46px;
    width: 1px; height: 60px; background: var(--brand);
  }

  .company { position: absolute; right: 40px; top: 34px; text-align: right; }
  .company__legal { font-size: 15px; font-weight: 700; color: var(--brand-dark); }
  .company__tagline { font-size: 9px; font-style: italic; color: var(--brand); margin-top: -2px; }
  .company__line {
    display: flex; justify-content: flex-end; align-items: center; gap: 6px;
    font-size: 10px; color: var(--brand-dark); margin-top: 3px;
  }
  .company__line svg { width: 9px; height: 10px; flex: none; }

  .ghost-mark {
    position: absolute; left: 260px; top: 300px;
    font-size: 230px; font-weight: 700; color: var(--ghost);
    line-height: 1; pointer-events: none;
  }

  .letter-body { position: absolute; left: 80px; top: 158px; width: 540px; }
  .letter-body__title { font-size: 12px; font-weight: 700; color: var(--brand); margin-bottom: 8px; }
  .letter-body p {
    font-size: 10px; line-height: 13px; color: var(--ink);
    text-align: justify; margin-bottom: 17px;
  }

  .closing { position: absolute; left: 92px; top: 758px; }
  .closing__greeting { font-size: 12px; color: var(--ink-soft); }
  .closing__signature {
    font-family: "Kaushan Script", cursive;
    font-size: 17px; color: #333; margin: 8px 0 6px 18px;
  }
  .closing__name { font-size: 16px; font-weight: 700; color: var(--brand); }
  .closing__title { font-size: 9px; color: var(--ink); margin-top: 2px; }
  .closing__contact { font-size: 9px; color: var(--ink); margin-top: 6px; line-height: 14px; }
</style>
</head>
<body>
<main class="letterhead">
  <svg class="band band--top" viewBox="0 0 707 14" preserveAspectRatio="none" aria-hidden="true">
    <defs>
      <linearGradient id="topFade" x1="0" x2="1" y1="0" y2="0">
        <stop offset="0" stop-color="#0d5aa7"/>
        <stop offset="0.75" stop-color="#6db3e6"/>
        <stop offset="1" stop-color="#4a98d6"/>
      </linearGradient>
    </defs>
    <polygon points="0,0 428,0 418,14 0,14" fill="url(#topFade)"/>
    <polygon points="436,0 707,0 707,14 426,14" fill="#0a4790"/>
  </svg>

  <div class="brand">
    <div class="brand__name">KMR</div>
    <div class="brand__cvr">CVR. NR. 58117904</div>
  </div>
  <div class="divider"></div>

  <header class="company">
    <div class="company__legal">Kestrel Meridian Rowe ApS</div>
    <div class="company__tagline">Shaping Lasting Gains</div>
    <div class="company__line">
      <span>Your Address, Street No., Denmark</span>
      <svg viewBox="0 0 10 12"><path d="M5 0a4 4 0 0 1 4 4c0 3-4 8-4 8S1 7 1 4a4 4 0 0 1 4-4z" fill="#0d5aa7"/><circle cx="5" cy="4" r="1.5" fill="#fff"/></svg>
    </div>
    <div class="company__line">
      <span>www.yourwebsite.com</span>
      <svg viewBox="0 0 10 10"><circle cx="5" cy="5" r="4.2" fill="#0d5aa7"/></svg>
    </div>
  </header>

  <div class="ghost-mark" aria-hidden="true">KMR</div>

  <section class="letter-body">
    <h2 class="letter-body__title">Lorem ipsum</h2>
    <p>Lorem ipsum dolor, consectetuer adipiscing elit, sed diam nonummy nibh euismod tincidunt ut laoreet dolore magna aliquam erat volutpat. Ut wisi enim ad minim veniam, quis nostrud exerci tation ullamcorper suscipit lobortis nisl ut aliquip ex ea commodo consequat. Duis autem vel eum iriure dolor in hendrerit in vulputate velit esse molestie consequat, vel illum dolore eu feugiat nulla facilisis minim</p>
    <p>Lorem ipsum dolor, consectetuer adipiscing elit, sed diam nonummy nibh euismod tincidunt ut laoreet dolore magna aliquam erat volutpat. Ut wisi enim ad minim veniam, quis nostrud exerci tation ullamcorper suscipit lobortis nisl ut aliquip ex ea commodo consequat. Duis autem vel eum iriure dolor in hendrerit in vulputate velit esse molestie consequat, vel illum dolore eu feugiat nulla facilisis minim</p>
    <p>Lorem ipsum dolor, consectetuer adipiscing elit, sed diam nonummy nibh euismod tincidunt ut laoreet dolore magna aliquam erat volutpat. Ut wisi enim ad minim veniam, quis nostrud exerci tation ullamcorper suscipit lobortis nisl ut aliquip ex ea commodo consequat. Duis autem vel eum iriure dolor in hendrerit in vulputate velit esse molestie consequat, vel illum dolore eu feugiat nulla facilisis minim</p>
    <p>Lorem ipsum dolor, consectetuer adipiscing elit, sed diam nonummy nibh euismod tincidunt ut laoreet dolore magna aliquam erat volutpat. Ut wisi enim ad minim veniam, quis nostrud exerci tation ullamcorper suscipit lobortis nisl ut aliquip ex ea commodo consequat. Duis autem vel eum iriure dolor in hendrerit in vulputate velit esse molestie consequat, vel illum dolore eu feugiat nulla facilisis minim</p>
    <p>Lorem ipsum dolor, consectetuer adipiscing elit, sed diam nonummy nibh euismod tincidunt ut laoreet dolore magna aliquam erat volutpat. Ut wisi enim ad minim veniam, quis nostrud exerci tation ullamcorper suscipit lobortis nisl ut aliquip ex ea commodo consequat. Duis autem vel eum iriure dolor in hendrerit in vulputate velit esse molestie consequat, vel illum dolore eu feugiat nulla facilisis minim</p>
    <p>Lorem ipsum dolor, consectetuer adipiscing elit, sed diam nonummy nibh euismod tincidunt ut laoreet dolore magna aliquam erat volutpat. Ut wisi enim ad minim veniam, quis nostrud exerci tation ullamcorper suscipit lobortis nisl ut aliquip ex ea commodo consequat. Duis autem vel eum iriure dolor in hendrerit in vulputate velit esse molestie consequat, vel illum dolore eu feugiat nulla facilisis minim</p>
    <p>Lorem ipsum dolor, consectetuer adipiscing elit, sed diam nonummy nibh euismod tincidunt ut laoreet dolore magna aliquam erat volutpat. Ut wisi enim ad minim veniam, quis nostrud exerci tation ullamcorper suscipit lobortis nisl ut aliquip ex ea commodo consequat. Duis autem vel eum iriure dolor in hendrerit in vulputate velit esse molestie consequat, vel illum dolore eu feugiat nulla facilisis minim</p>
    <p>Lorem ipsum dolor, consectetuer adipiscing elit, sed diam nonummy nibh euismod tincidunt ut laoreet dolore magna aliquam erat volutpat. Ut wisi enim ad minim veniam, quis nostrud exerci tation ullamcorper suscipit lobortis nisl ut</p>
  </section>

  <footer class="closing">
    <div class="closing__greeting">Yours Sincerely,</div>
    <div class="closing__signature">Yours Signature</div>
    <div class="closing__name">Your full name</div>
    <div class="closing__title">Managing Director</div>
    <div class="closing__contact">(00) 00-00-00-00<br>yourname@yourwebsite.com</div>
  </footer>

  <svg class="band band--bottom" viewBox="0 0 707 14" preserveAspectRatio="none" aria-hidden="true">
    <defs>
      <linearGradient id="bottomFade" x1="0" x2="1" y1="0" y2="0">
        <stop offset="0" stop-color="#4a98d6"/>
        <stop offset="0.25" stop-color="#6db3e6"/>
        <stop offset="1" stop-color="#0d5aa7"/>
      </linearGradient>
    </defs>
    <polygon points="0,0 290,0 280,14 0,14" fill="#0a4790"/>
    <polygon points="298,0 707,0 707,14 288,14" fill="url(#bottomFade)"/>
  </svg>
</main>
</body>
</html>
```